Need a stunning home page for Car rental company

For a client, I need a slick and sumber home page design. It is a small, local car rental company, with a handful of cars available for rent.
Selling points: affordable lease, availability, always clean cars
The design should be:
- flat and modern
- no, or very few animations/sliders
- CTA: booking form for renting a car.
- 3 featured cars with images and facts (see website) with button to read more about the car.
- fullscreen background video can be an option
- main colour: #efba01
The site is under construction here:
http://solvikutleie.hammerlia.no/
Delivery requirements:
I need a layered & well organised PSD file delivered.

```html
<!DOCTYPE html>
<html lang="en">
<head>
<meta charset="utf-8">
<title>Solvikutleie – Car Rental</title>
<link href="https://fonts.googleapis.com/css2?family=Quicksand:wght@400;500;600;700&family=Open+Sans:wght@400;600&display=swap" rel="stylesheet">
<style>
:root{
  --brand:#efba01;
  --brand-dark:#d9a700;
  --ink:#2b2b2b;
  --muted:#6b6b6b;
  --line:#dddddd;
  --paper:#ffffff;
  --soft:#f9f9f9;
  --footer:#f0f0f0;
  --head:"Quicksand",sans-serif;
  --body:"Open Sans",sans-serif;
}
*{box-sizing:border-box;margin:0;padding:0}
html,body{width:818px;height:1200px;overflow:hidden;background:var(--paper)}
body{position:relative;font-family:var(--body);color:var(--ink)}
.abs{position:absolute}

/* header */
.site-header{left:0;top:0;width:818px;height:69px;background:var(--paper)}
.brand{left:110px;top:24px;font-family:var(--head);font-weight:700;font-size:21px;letter-spacing:1px;color:var(--brand)}
.lang{left:638px;top:11px;width:58px;height:16px;border:1px solid var(--line);border-radius:2px;font-size:7px;display:flex;align-items:center;gap:4px;padding-left:6px;color:var(--ink)}
.lang .flag{width:10px;height:7px;background:#3b5ba5}
.phone{left:622px;top:41px;display:flex;align-items:center;gap:3px;font-family:var(--head);font-size:13px;font-weight:500;color:#444}

/* nav */
.main-nav{left:0;top:69px;width:818px;height:33px;background:var(--brand);display:flex;justify-content:center}
.main-nav a{color:#fff;text-decoration:none;font-family:var(--head);font-weight:600;font-size:10.5px;padding:0 11.5px;line-height:33px;border-left:1px solid rgba(255,255,255,.35)}
.main-nav a:first-child{border-left:none}

/* hero */
.hero{left:0;top:102px;width:818px;height:326px;background:linear-gradient(100deg,#f4e7c4 0%,#cfd6d8 35%,#8c99a6 60%,#b9c2c8 85%,#e1e4e3 100%)}
.play{left:391px;top:241px;width:38px;height:38px;border-radius:50%;background:#fff}
.dots{left:389px;top:409px;display:flex;gap:3px}
.dots span{width:9px;height:9px;border-radius:50%;background:#fff}
.booking{left:537px;top:185px;width:165px;height:153px;background:var(--paper);border-radius:2px;box-shadow:0 1px 4px rgba(0,0,0,.15);padding:14px 14px}
.booking h2{font-family:var(--head);font-weight:500;font-size:14px;color:var(--ink)}
.booking p{font-size:6.5px;color:#999;margin:2px 0 8px}
.field{height:17px;border:1px solid var(--line);margin-bottom:4px;font-size:6px;color:#999;padding-left:7px;line-height:15px;position:relative}
.field svg{position:absolute;right:5px;top:5px}
.btn{display:inline-block;background:var(--brand);color:#fff;font-family:var(--head);font-weight:600;text-transform:uppercase}
.booking .btn{margin-top:2px;font-size:9px;padding:0 12px;line-height:22px}

/* about */
.about{left:0;top:428px;width:818px;height:196px;text-align:center}
.about h2{margin-top:38px;font-family:var(--head);font-weight:500;font-size:21px;color:var(--ink)}
.about .lead{margin-top:6px;font-size:10px;color:#555}
.about .copy{width:545px;margin:7px auto 0;font-size:7.3px;line-height:11.5px;color:#777}
.about .copy+.copy{margin-top:8px}

/* featured */
.featured{left:0;top:624px;width:818px;height:307px;background:var(--brand)}
.featured h2{position:absolute;top:27px;width:100%;text-align:center;font-family:var(--head);font-weight:500;font-size:21px;color:#fff}
.car-card{top:66px;width:188px;height:206px;background:linear-gradient(#fff 70%,#f3f3f3)}
.car-photo{height:98px}
.car-card h3{font-family:var(--head);font-weight:500;font-size:12px;margin:9px 14px 5px}
.car-card p{font-size:6.5px;line-height:11.5px;color:#666;margin:0 14px}
.car-card .btn{margin:6px 14px 0;font-size:7px;width:65px;line-height:18px;text-align:center}

/* blogs */
.blogs{left:0;top:931px;width:818px;height:195px;background:var(--soft)}
.blogs h2{position:absolute;left:114px;top:37px;font-family:var(--head);font-weight:500;font-size:20px}
.post{top:75px;width:180px}
.post h3{font-family:var(--head);font-weight:500;font-size:10.5px;color:var(--brand)}
.post p{font-size:6.8px;line-height:11.7px;color:#777;margin-top:3px}
.post a{display:block;margin-top:5px;font-size:7.5px;color:#555;text-decoration:none}

/* footer */
.site-footer{left:0;top:1126px;width:818px;height:74px;background:var(--footer)}
.foot-links{left:115px;top:24px;font-family:var(--head);font-weight:500;font-size:8.8px;color:#333}
.foot-links span{margin:0 4px;color:#555}
.legal{left:115px;top:41px;font-size:6.5px;color:#777}
.social{left:626px;top:23px;display:flex;gap:6px}
.social span{width:13px;height:13px;border-radius:1px}
</style>
</head>
<body>

<header class="site-header abs">
  <div class="brand abs">SOLVIKUTLEIE</div>
  <div class="lang abs"><span class="flag"></span>English
    <svg width="6" height="4" viewBox="0 0 6 4"><path d="M0 0h6L3 4z" fill="#666"/></svg></div>
  <div class="phone abs">
    <svg width="14" height="14" viewBox="0 0 16 16"><circle cx="8" cy="8" r="7" fill="none" stroke="#555" stroke-width="1.2"/><path d="M5.6 4.5l1.3 1.5-.7 1c.5 1 1.3 1.8 2.3 2.3l1-.7 1.5 1.3-.8 1.3c-2.6-.3-4.9-2.6-5.2-5.2z" fill="#555"/></svg>
    55 51 23 40
  </div>
</header>

<nav class="main-nav abs">
  <a>HJEM</a><a>BILPARKEN VÅR</a><a>TJENESTER</a><a>KONTAKT OSS</a><a>BLOG</a><a>PAGE TEMPLATES</a><a>ABOUT US</a>
</nav>

<section class="hero abs" role="img" aria-label="Background video still: woman leaning happily out of a silver car window in sunlight">
  <div class="play abs">
    <svg width="38" height="38" viewBox="0 0 38 38"><path d="M15 11l12 8-12 8z" fill="#111"/></svg>
  </div>
  <div class="dots abs" style="top:307px;left:389px"><span></span><span></span><span></span><span></span></div>
</section>

<form class="booking abs">
  <h2>Booking Form</h2>
  <p>Curabitur iaculis tempus eros Curabit</p>
  <div class="field">Car Name</div>
  <div class="field">Choose Category
    <svg width="7" height="5" viewBox="0 0 7 5"><path d="M.5.5l3 3 3-3" fill="none" stroke="#555"/></svg></div>
  <div class="field">Brand Name</div>
  <span class="btn">Rent a car</span>
</form>

<section class="about abs">
  <h2>Little About Our Company</h2>
  <p class="lead">Mauris vel lacus vitae felis vestibulum volutpat Etiam est nunc venenatis in tristique eu imperdiet</p>
  <p class="copy">Cum sociis natoque penatibus et magnis dis parturient montes nascetur ridiculus mus In iaculis facilisis massa Etiam eu urna Sed porta Suspendisse quam leo molestie sed luctus quis feugiat in pede Fusce tellus Sed metus augue convallis et vehicula ut pulvinar eu ante Integer orciVivamus porttitor purus nisi eleifend libero a tempus libero lectus feugiat felis Morbi diam mauris viverra in gravida eu mattis in ante Morbi eget ar</p>
  <p class="copy">cu Morbi porta libero id ullamcorper nonummy nibh ligula pulvinar metus eget consectetuer augue nisi quis lacus Ut ac mi quis lacus mollis aliquam Curabitur iaculis tempus eros Curabitur vel mi sit amet magna malesuada ultrices Ut nisi erat fermentum</p>
</section>

<section class="featured abs">
  <h2>FEATURED CARS</h2>
  <article class="car-card abs" style="left:114px">
    <div class="car-photo" role="img" aria-label="White cargo van parked on gravel" style="background:linear-gradient(#c9ccce,#eef0f1 55%,#9a9890)"></div>
    <h3>Varebilen</h3>
    <p>Mauris vel lacus vitae felis vestibulum volutpat Etiam est nunc venenatis in tristique eu imperdiet ac nisl Cum sociis natoque penatibus et magnis-metus augue convallis et vehicula</p>
    <span class="btn">Read more</span>
  </article>
  <article class="car-card abs" style="left:315px">
    <div class="car-photo" role="img" aria-label="Grey SUV on a coastal road" style="background:linear-gradient(#5d8ab8,#8aa2b5 45%,#6c6f73 70%,#b8bab8)"></div>
    <h3>Curabitur iaculis</h3>
    <p>Mauris vel lacus vitae felis vestibulum volutpat Etiam est nunc venenatis in tristique eu imperdiet ac nisl Cum sociis natoque penatibus et magnis-metus augue convallis et vehicula</p>
    <span class="btn">Read more</span>
  </article>
  <article class="car-card abs" style="left:517px">
    <div class="car-photo" role="img" aria-label="Silver sedan parked among palm trees" style="background:linear-gradient(#a9c3d8,#c9cfd0 40%,#8b8e90 70%,#c2c2bc)"></div>
    <h3>Morbi Porta libero</h3>
    <p>Mauris vel lacus vitae felis vestibulum volutpat Etiam est nunc venenatis in tristique eu imperdiet ac nisl Cum sociis natoque penatibus et magnis-metus augue convallis et vehicula</p>
    <span class="btn">Read more</span>
  </article>
</section>

<section class="blogs abs">
  <h2>Recent Blogs</h2>
  <article class="post abs" style="left:116px">
    <h3>Morbi diam mauris</h3>
    <p>Mauris vel lacus vitae felis vestibulum volutpat Etiam est nunc venenatis in tristique eu imperdiet ac nisl Cum sociis natoque penatibus et</p>
    <a>Learn More</a>
  </article>
  <article class="post abs" style="left:319px">
    <h3>Suspendisse quam leo molestie</h3>
    <p>Mauris vel lacus vitae felis vestibulum volutpat Etiam est nunc venenatis in tristique eu imperdiet ac nisl Cum sociis natoque penatibus et</p>
    <a>Learn More</a>
  </article>
  <article class="post abs" style="left:522px">
    <h3>Fusce tellus Sed metus</h3>
    <p>Mauris vel lacus vitae felis vestibulum volutpat Etiam est nunc venenatis in tristique eu imperdiet ac nisl Cum sociis natoque penatibus et</p>
    <a>Learn More</a>
  </article>
</section>

<footer class="site-footer abs">
  <div class="foot-links abs">About Us<span>|</span>Capabilities / Offerings<span>|</span>Join Our Team<span>|</span>Portfolio<span>|</span>Clients<span>|</span>Contact Us</div>
  <div class="legal abs">© 2014 Company Name &nbsp;All right reserved &nbsp;Term of Use</div>
  <div class="social abs" aria-label="Social links">
    <span style="background:#3b5998"></span><span style="background:#33b5e5"></span><span style="background:#0e76a8"></span><span style="background:#f0842c"></span>
  </div>
</footer>

</body>
</html>
```